Navoro & Omvar Automotive Repair Shop. Need a new website design.

We specialize in Navoro & Omvar auto repair, but also work on other Asian import vehicles. We have been in business for 7 years and pride ourselves on high quality auto repair that is fixed right the first time. Would like the automotive repair website to incorporate the colors black, red and white if possible and have our logo and some Navoro and Omvar vehicles included in the website.

Target Market(s)

Navoro & Omvar vehicle owners

Industry/Entity Type

Automotive Repair

Coding

Coded - Design and coding required

Number of Pages Required

5+ page

Colors
EB3D1F
EC4F4E
F09395
F8D3D4
FCEDEE

Requirements
Must have
• Home, Services, Contact Us, Schedule appointment, and a gallery tab that I can add shop pictures to when completed.
Nice to have
• Would like to see example pictures of job next to each service listed.
Should not have
• Service not related to auto repair. Ex. auto detailing, towing, car wash

```html
<!DOCTYPE html>
<html lang="en">
<head>
<meta charset="utf-8">
<title>Kestrel Automotive</title>
<link rel="stylesheet" href="https://fonts.googleapis.com/css2?family=Krona+One&family=Poppins:wght@400;500;600;700&display=swap">
<style>
:root{
  --red:#e3141b;
  --red-deep:#b30d12;
  --black:#070707;
  --ink:#1b1b1b;
  --grey:#f0f0f0;
  --tile:#ebebeb;
  --white:#ffffff;
  --muted:#555;
  --navy:#1c2a55;
}
*{box-sizing:border-box;margin:0;padding:0}
html,body{width:1200px;height:3987px;overflow:hidden}
body{position:relative;background:var(--white);font-family:"Poppins",sans-serif;color:var(--ink)}
.abs{position:absolute}
.chrome{font-family:"Krona One",sans-serif;font-weight:400;
  background:linear-gradient(180deg,#ffffff 0%,#a8a8a8 50%,#5e5e5e 52%,#e6e6e6 100%);-webkit-background-clip:text;background-clip:text;color:transparent}
.chrome.dark{background:linear-gradient(180deg,#8a8a8a 0%,#3a3a3a 50%,#111 52%,#7a7a7a 100%);-webkit-background-clip:text;background-clip:text}
.title{position:absolute;left:0;width:1200px;text-align:center;font-size:27px;letter-spacing:2px}
.rule{position:absolute;height:3px;width:46px;background:var(--red)}
.btn{position:absolute;background:var(--red);color:var(--white);font-family:"Krona One",sans-serif;font-size:14px;
  display:flex;align-items:center;justify-content:center;transform:skewX(-14deg);border-left:5px solid var(--white);box-shadow:-6px 0 0 var(--black)}
.btn span{transform:skewX(14deg)}
.photo{position:absolute;overflow:hidden}
.brand-mark{position:absolute;display:flex;align-items:center;gap:8px;color:var(--white);font-family:"Krona One",sans-serif}
.brand-mark i{display:block;width:14px;height:14px;background:var(--red);border-radius:50%;flex:none}
/* header */
.search{left:457px;top:23px;width:271px;height:34px;background:var(--white);border-radius:2px;transform:skewX(-12deg)}
.search span{position:absolute;left:16px;top:7px;font-size:14px;color:#666;transform:skewX(12deg)}
.search b{position:absolute;right:0;top:0;width:38px;height:34px;background:var(--red)}
.phone{left:800px;top:36px;color:var(--white);font-size:16px;display:flex;align-items:center;gap:14px}
.social{display:flex;gap:9px}
.social i{display:block;width:26px;height:26px;border-radius:50%;background:var(--red)}
.social i.g{background:#d9d9d9}
.nav{left:320px;top:90px;width:774px;display:flex;justify-content:space-between;color:var(--white);font-size:15px}
.nav a.on{color:var(--red);text-decoration:underline}
.hero-line{left:104px;top:134px;width:992px;height:1px;background:#333}
.welcome{left:104px;top:250px;color:var(--red);font-family:"Krona One",sans-serif;font-size:21px;letter-spacing:1px}
.hero-name{left:104px;top:288px;font-size:37px;line-height:52px;letter-spacing:2px}
/* about */
.about-text{left:640px;top:782px;width:430px}
.about-text h2{font-size:27px;letter-spacing:2px}
.about-text .lead{font-family:"Krona One",sans-serif;font-size:13.5px;line-height:22px;margin-top:34px}
.about-text .body{font-size:13px;line-height:21px;color:var(--muted);margin-top:14px}
/* services */
.card{position:absolute;top:1363px;width:232px;height:287px;display:flex;flex-direction:column;justify-content:flex-end;align-items:center;text-align:center;color:var(--white);padding:0 14px 46px}
.card h3{font-family:"Krona One",sans-serif;font-size:16px;line-height:24px;font-weight:400;position:relative}
.card p{font-size:12px;line-height:22px;margin-top:8px}
/* clients */
.clients-lead{left:200px;top:1950px;width:800px;text-align:center;font-family:"Krona One",sans-serif;font-size:14px;line-height:22px}
.grid{left:104px;top:2025px;width:992px;display:grid;grid-template-columns:repeat(4,1fr);gap:5px}
.grid div{height:84px;background:var(--tile);display:flex;align-items:center;justify-content:center;font-weight:600;font-size:19px;letter-spacing:2px;color:var(--navy)}
.grid div.r{color:var(--red)}
/* contact */
.field{position:absolute;border:1px solid #d5d5d5;color:var(--white);font-size:14px;padding:12px 10px;height:44px}
.field.sel::after{content:"";position:absolute;right:14px;top:15px;width:6px;height:6px;border-right:1.5px solid #fff;border-bottom:1.5px solid #fff;transform:rotate(45deg)}
.choice{position:absolute;top:3564px;display:flex;align-items:center;gap:8px;color:var(--white);font-family:"Krona One",sans-serif;font-size:16px}
.choice i{display:block;width:20px;height:20px;border-radius:50%;background:#2b2b2b}
.choice i.on{background:var(--red)}
/* footer */
.fnav{left:494px;top:3772px;width:640px;display:flex;justify-content:space-between;font-size:15px;color:var(--ink)}
.info{position:absolute;top:3826px}
.info h4{font-family:"Krona One",sans-serif;color:var(--red);font-size:16px;font-weight:400}
.info p{font-size:12px;line-height:19px;margin-top:6px;color:var(--ink)}
.ico{position:absolute;top:3834px;width:42px;height:42px;border-radius:50%;background:var(--red)}
.copy{left:104px;top:3948px;font-size:11.5px;color:var(--ink)}
</style>
</head>
<body>

<!-- HERO -->
<svg class="abs" style="left:0;top:0" width="1200" height="690" viewBox="0 0 1200 690" aria-hidden="true">
  <defs><linearGradient id="heroFill" x1="0" y1="0" x2="0" y2="1"><stop offset="0" stop-color="#141414"/><stop offset="1" stop-color="#000"/></linearGradient></defs>
  <polygon points="0,0 1200,0 1200,530 600,680 0,530" fill="#b30d12"/>
  <polygon points="0,0 1200,0 1200,518 600,655 0,528" fill="url(#heroFill)"/>
</svg>
<div class="brand-mark" style="left:104px;top:50px;font-size:15px"><i></i>KESTREL</div>
<div class="search abs"><span>Search...</span><b></b></div>
<div class="phone abs">
  <svg width="30" height="30" viewBox="0 0 24 24" fill="none" stroke="#fff" stroke-width="1.4"><path d="M5 3h4l2 5-2.5 1.5a11 11 0 0 0 6 6L16 13l5 2v4a2 2 0 0 1-2 2A17 17 0 0 1 3 5a2 2 0 0 1 2-2z"/></svg>
  <span>+1 555 014 2200</span>
  <div class="social" style="margin-left:6px"><i aria-label="Social link"></i><i class="g" aria-label="Social link"></i><i class="g" aria-label="Social link"></i></div>
</div>
<nav class="nav abs"><a class="on">Home</a><span>|</span><a>Our Services</a><span>|</span><a>Directions</a><span>|</span><a>About Us</a><span>|</span><a>Contact Us</a></nav>
<div class="hero-line abs"></div>
<div class="welcome abs">WELCOME TO</div>
<div class="hero-name chrome abs">KESTREL<br>AUTOMOTIVE</div>
<div class="btn" style="left:104px;top:410px;width:290px;height:40px"><span>Schedule An Appointment</span></div>
<div class="photo" role="img" aria-label="Red Navoro crossover SUV, front three-quarter view, on a dark studio background" style="left:510px;top:258px;width:650px;height:352px;border-radius:180px 200px 28px 28px;background:linear-gradient(165deg,#e5262a 0%,#c4151a 45%,#7d0a0d 80%,#2a0405 100%)"></div>
<div class="abs" role="img" aria-label="Certification badge" style="left:690px;top:222px;width:70px;height:70px;border-radius:50%;background:#2c3a8c;border:3px solid #0d1640"></div>

<!-- ABOUT -->
<div class="abs" role="img" aria-label="Kestrel Automotive emblem" style="left:140px;top:760px;width:410px;height:355px;display:flex;align-items:center;justify-content:center">
  <div class="brand-mark" style="position:static;color:var(--ink);font-size:40px;gap:16px"><i style="width:34px;height:34px"></i>KESTREL</div>
</div>
<div class="about-text abs">
  <h2 class="chrome dark">ABOUT US</h2>
  <p class="lead">Kestrel Automotive is a locally owned and operated auto repair shop in Brookhaven that offers comprehensive car care and services for Navoro &amp; Omvar and all other Asian imports vehicles.</p>
  <p class="body">Led by a certified master technician with 20 years experience working for Navoro &amp; Omvar dealerships, our auto shop is your go to facility for everything from factory auto maintenance,</p>
</div>
<div class="rule" style="left:640px;top:823px"></div>
<div class="btn" style="left:646px;top:1044px;width:150px;height:40px"><span>Read More</span></div>

<!-- SERVICES -->
<svg class="abs" style="left:0;top:1192px" width="1200" height="625" viewBox="0 0 1200 625" aria-hidden="true">
  <polygon points="0,0 1200,0 1200,505 600,620 0,505" fill="#b30d12"/>
  <polygon points="0,0 1200,0 1200,500 600,592 0,513" fill="#060606"/>
</svg>
<h2 class="title chrome" style="top:1292px">OUR SERVICES</h2>
<div class="rule" style="left:577px;top:1336px"></div>
<div class="card" role="img" aria-label="Mechanic working under an open hood during an oil change" style="left:102px;background:linear-gradient(180deg,#b9b4ae 0%,#6d665f 45%,#2a2623 100%);clip-path:polygon(0 0,100% 8%,100% 100%,0 88%)"><h3>Oil Changes</h3></div>
<div class="card" style="left:353px;background:linear-gradient(180deg,#e3141b,#b30d12);clip-path:polygon(0 8%,100% 0,100% 100%,0 92%);padding-bottom:40px;justify-content:center">
  <h3>Computer<br>Diagnostics</h3><p>Lorem ipsum dolor sit amet, con adipiscing elit, incididunt ut aliqua.</p></div>
<div class="card" role="img" aria-label="Technician checking engine wiring and electrical parts" style="left:607px;background:linear-gradient(180deg,#8a7462 0%,#46403e 45%,#15161a 100%);clip-path:polygon(0 8%,100% 0,100% 92%,0 100%)"><h3>Electrical<br>Specialists</h3></div>
<div class="card" role="img" aria-label="Mechanic mounting an alloy wheel and tire" style="left:859px;background:linear-gradient(180deg,#9aa2ab 0%,#4d5157 45%,#17181a 100%);clip-path:polygon(0 8%,100% 0,100% 88%,0 100%)"><h3>Tires</h3></div>
<div class="btn" style="left:528px;top:1680px;width:148px;height:40px"><span>View More</span></div>

<!-- CLIENTS -->
<h2 class="title chrome dark" style="top:1894px">CLIENTS</h2>
<div class="rule" style="left:577px;top:1936px"></div>
<p class="clients-lead abs">Kestrel Automotive specializes in Navoro &amp; Omvar auto repair but also service and repair the following makes:</p>
<div class="grid abs">
  <div class="r">HARLO</div><div>AVENZA</div><div>NORRIN</div><div>ILUMAR</div>
  <div>HESTARA</div><div>KOVA</div><div class="r" style="font-size:14px">MIRAKO MOTORS</div><div>MARZO</div>
</div>

<!-- GALLERY -->
<div class="abs" style="left:0;top:2276px;width:1200px;height:680px;background:var(--grey)"></div>
<h2 class="title chrome dark" style="top:2378px">GALLERY</h2>
<div class="rule" style="left:577px;top:2420px"></div>
<div class="photo" role="img" aria-label="Bright service bay with cars on lifts and two technicians walking" style="left:104px;top:2462px;width:404px;height:421px;background:linear-gradient(180deg,#a9b4c0 0%,#d7dee6 45%,#b8c6d4 70%,#8fa2b6 100%)"></div>
<div class="photo" role="img" aria-label="Mechanic inspecting an engine bay" style="left:519px;top:2462px;width:283px;height:207px;background:linear-gradient(160deg,#a8a4a0 0%,#55524f 50%,#1c1c1d 100%)"></div>
<div class="photo" role="img" aria-label="Technician with a tablet checking an engine" style="left:813px;top:2462px;width:283px;height:207px;background:linear-gradient(160deg,#9c7c5c 0%,#5a4a40 50%,#221d1b 100%)"></div>
<div class="photo" role="img" aria-label="Mechanic repairing an engine component" style="left:519px;top:2680px;width:283px;height:203px;background:linear-gradient(160deg,#8a9cb2 0%,#4a5366 50%,#1f2230 100%)"></div>
<div class="photo" role="img" aria-label="Technician fitting a wheel in a workshop" style="left:813px;top:2680px;width:283px;height:203px;background:linear-gradient(160deg,#d49a5c 0%,#7a5a40 50%,#241c18 100%)"></div>

<!-- CONTACT -->
<div class="abs" style="left:0;top:2930px;width:1200px;height:762px;background:var(--black)"></div>
<svg class="abs" style="left:0;top:2920px" width="1200" height="120" viewBox="0 0 1200 120" aria-hidden="true">
  <polygon points="0,0 1200,0 1200,15 600,110 0,15" fill="#c4141a"/>
  <polygon points="0,0 1200,0 1200,8 600,85 0,24" fill="#f0f0f0"/>
</svg>
<h2 class="title chrome" style="top:3130px">CONTACT US</h2>
<div class="rule" style="left:577px;top:3175px"></div>
<div class="field" style="left:125px;top:3220px;width:308px">Name</div>
<div class="field" style="left:446px;top:3220px;width:308px">Phone</div>
<div class="field" style="left:765px;top:3220px;width:308px">Email Address</div>
<div class="field sel" style="left:125px;top:3283px;width:308px">Year</div>
<div class="field sel" style="left:446px;top:3283px;width:308px">Make</div>
<div class="field sel" style="left:765px;top:3283px;width:308px">Model</div>
<div class="field" style="left:125px;top:3345px;width:948px;height:180px">Message</div>
<div class="choice" style="left:375px"><i class="on"></i>Service</div>
<div class="choice" style="left:497px"><i></i>Repair</div>
<div class="btn" style="left:626px;top:3556px;width:112px;height:40px"><span>Submit</span></div>

<!-- FOOTER -->
<div class="brand-mark" style="left:104px;top:3808px;color:var(--ink);font-size:18px"><i></i>KESTREL</div>
<div class="abs" role="img" aria-label="Local award badge" style="left:328px;top:3795px;width:82px;height:82px;border-radius:50%;background:#dfe9f6"></div>
<nav class="fnav abs"><span>Home</span><span>|</span><span>Our Services</span><span>|</span><span>Directions</span><span>|</span><span>About Us</span><span>|</span><span>Contact Us</span></nav>
<div class="info" style="left:448px"><h4>Location :</h4><p>418 Harbor Point Drive #5 Brookhaven,<br>TX 75090</p></div>
<div class="ico" style="left:676px"><svg width="42" height="42" viewBox="0 0 42 42"><path d="M15 13h4l2 4-2 1.5a8 8 0 0 0 4.5 4.5L25 21l4 2v3.5a1.6 1.6 0 0 1-1.6 1.6A13 13 0 0 1 13.9 14.6 1.6 1.6 0 0 1 15 13z" fill="#fff"/></svg></div>
<div class="info" style="left:740px"><h4>Call Us :</h4><p>OFFICE. 555.013.4410<br>CELL. 555.017.2286</p></div>
<div class="ico" style="left:870px"><svg width="42" height="42" viewBox="0 0 42 42"><rect x="12" y="15" width="18" height="13" rx="1.5" fill="#fff"/><path d="M12 16l9 6 9-6" stroke="#e3141b" stroke-width="1.6" fill="none"/></svg></div>
<div class="info" style="left:936px"><h4>Email :</h4><p>KestrelAutoLLC@mailbox.com</p></div>
<div class="abs" style="left:104px;top:3936px;width:992px;height:1px;background:#ddd"></div>
<p class="copy abs">©Copyrights 2024 &nbsp;Kestrel Automotive LLC | All Rights Reserved</p>
<div class="social abs" style="left:996px;top:3950px"><i aria-label="Social link"></i><i class="g" aria-label="Social link"></i><i class="g" aria-label="Social link"></i></div>

</body>
</html>
```